Business Card Design needed for start up company Halvora

In need of a new business card designed for a start up company based in Sydney, Halvora is a new start up innovative Company, our mission it to make property accessible for everyday Australian and to become the leading Real Estate platform in Australia. We want it to be fresh and clean.

Industry/Entity Type

Financial

Contact Information for Business Card

Section for Name
Section for Title

HALVORA - The Strength of Pooling
Mobile:
Direct:

Font styles to use
Sans Serif

Colors
33a6d7
0692cd
0255a3
ffffff

Requirements
Must have
• Logo, all business card details

```html
<!DOCTYPE html>
<html lang="en">
<head>
<meta charset="utf-8">
<title>Halvora Business Card</title>
<link rel="stylesheet" href="https://fonts.googleapis.com/css2?family=Jost:wght@400;500;600;700&display=swap">
<style>
  :root {
    --sky: #2a9bd6;
    --sky-light: #33a6d7;
    --navy: #1e3f7a;
    --ink: #4a4a4a;
    --paper: #f4f4f4;
    --white: #ffffff;
    --backdrop: #e9e6e2;
  }
  * { margin: 0; padding: 0; box-sizing: border-box; }
  html, body {
    width: 1200px;
    height: 960px;
    overflow: hidden;
    background: var(--backdrop);
    font-family: "Jost", sans-serif;
  }
  .stage { position: relative; width: 1200px; height: 960px; }
  .card {
    position: absolute;
    width: 600px;
    height: 342px;
    border-radius: 18px;
    overflow: hidden;
    box-shadow: 0 4px 8px rgba(0,0,0,0.35);
  }
  .card-front { left: 216px; top: 131px; background: var(--paper); }
  .card-back { left: 381px; top: 504px; background: var(--sky); }
  .corner-art { position: absolute; inset: 0; width: 600px; height: 342px; }

  .holder { position: absolute; left: 28px; top: 28px; }
  .holder-name {
    font-size: 21px; font-weight: 600; color: var(--navy);
    letter-spacing: 0.5px; line-height: 26px;
  }
  .holder-title {
    font-size: 15px; font-weight: 400; color: var(--sky);
    letter-spacing: 0.3px; line-height: 20px;
  }
  .holder-address {
    margin-top: 4px;
    font-size: 14px; color: var(--ink); line-height: 18px;
  }

  .brand { position: absolute; display: flex; align-items: center; }
  .brand-dot { border-radius: 50%; flex: none; }
  .brand-name { font-weight: 700; letter-spacing: 0.5px; line-height: 1; }
  .card-front .brand { left: 159px; top: 141px; gap: 10px; }
  .card-front .brand-dot { width: 82px; height: 82px; background: var(--sky); }
  .card-front .brand-name { font-size: 50px; color: var(--navy); }
  .card-back .brand { left: 124px; top: 115px; gap: 12px; }
  .card-back .brand-dot { width: 106px; height: 106px; background: var(--white); }
  .card-back .brand-name { font-size: 62px; color: var(--white); }

  .contact-list {
    position: absolute; right: 26px; top: 242px;
    list-style: none; text-align: right;
  }
  .contact-item {
    display: flex; justify-content: flex-end; align-items: center;
    gap: 8px; height: 19.5px;
    font-size: 14px; color: var(--ink);
  }
  .contact-icon { width: 14px; height: 14px; flex: none; fill: var(--navy); }

  .tagline {
    position: absolute; left: 0; right: 0; top: 284px;
    text-align: center; font-size: 16px; color: var(--white);
  }
</style>
</head>
<body>
<main class="stage">

  <section class="card card-front" aria-label="Business card front">
    <svg class="corner-art" viewBox="0 0 600 342" aria-hidden="true">
      <path d="M492 0 Q588 72 600 205 V0 Z" fill="var(--navy)"/>
      <path d="M462 0 Q582 58 597 238 Q584 92 478 0 Z" fill="var(--sky)"/>
      <path d="M0 188 Q18 298 122 342 H0 Z" fill="var(--navy)"/>
      <path d="M3 200 Q28 302 140 342 H124 Q22 300 3 200 Z" fill="var(--sky)"/>
    </svg>

    <div class="holder">
      <p class="holder-name">MARCUS DELANE</p>
      <p class="holder-title">CEO/FOUNDER</p>
      <p class="holder-address">4120 Wattle Grove<br>Parramatta, NSW 2150</p>
    </div>

    <div class="brand">
      <span class="brand-dot"></span>
      <span class="brand-name">HALVORA</span>
    </div>

    <ul class="contact-list">
      <li class="contact-item">612 555 0147
        <svg class="contact-icon" viewBox="0 0 16 16"><path d="M3.5 1 L6 1.5 L7 5 L5.3 6.3 Q6.6 9.2 9.7 10.7 L11 9 L14.5 10 L15 12.5 Q14 15 11.5 15 Q2 13 1 4.5 Q1 2 3.5 1 Z"/></svg>
      </li>
      <li class="contact-item">614 555 0283
        <svg class="contact-icon" viewBox="0 0 16 16"><path d="M4 0.5 H12 Q13 0.5 13 1.5 V14.5 Q13 15.5 12 15.5 H4 Q3 15.5 3 14.5 V1.5 Q3 0.5 4 0.5 Z M4.5 2.5 V12 H11.5 V2.5 Z M7 13 H9 V14.3 H7 Z"/></svg>
      </li>
      <li class="contact-item">marcus@halvora.com
        <svg class="contact-icon" viewBox="0 0 16 16"><path d="M1 4 L8 9 L15 4 V13 H1 Z M1.5 3 H14.5 L8 7.6 Z"/></svg>
      </li>
      <li class="contact-item">www.halvora.com
        <svg class="contact-icon" viewBox="0 0 16 16"><circle cx="8" cy="8" r="7"/><path d="M4 5 Q6 4 7 6 Q6 8 4.5 8 Z M9 9 Q11 8.5 12 10.5 Q10.5 12.5 9.5 12 Z" fill="var(--paper)"/></svg>
      </li>
    </ul>
  </section>

  <section class="card card-back" aria-label="Business card back">
    <div class="brand">
      <span class="brand-dot"></span>
      <span class="brand-name">HALVORA</span>
    </div>
    <p class="tagline">The Strength of Pooling</p>
  </section>

</main>
</body>
</html>
```